Elegant, High End Integrated Wellness Healthcare Practice

We need a brochure designed for an integrated mind-body wellness healthcare practice (www.quellarivecare.com) . This brochure will be used when we cold call prospects (physicians to refer to our office, and potential consumers to utilize our services). Our practice is geographically located in the middle Tennessee USA region, although we have plans to become an international company as many of our offerings can be accessed anywhere in the world. Ultimately our goal is to have this brochure used as a leave-behind in an effort to introduce our integrated offerings to increase market share. The final product brochure should be both elegant and serious, with clean lines but also convey warmth and trust, as individuals who are coming for our services have usually struggled with their health for a significant amount of time before finding our practice.
Updates

The design brief was very specific about providing a high-end science-based 2-page brochure (not flier). Several designs submitted were fliers. The other designs were heavy on yoga or "woo woo" non-science-based looking pictures. This is a flier to appeal to physicians and other healthcare providers. Therefore the design must speak science and evidence-based methods of mind and body wellness care. I would also like to appeal to the other designers I paid extra for their submissions and who have indicated they will "respond in the coming days."

```html
<!DOCTYPE html>
<html lang="en">
<head>
<meta charset="utf-8">
<title>Quellarive Care – Brochure Pages</title>
<link rel="stylesheet" href="https://fonts.googleapis.com/css2?family=Cinzel:wght@600;700&family=Lato:wght@400;700&display=swap">
<style>
  :root {
    --backdrop: #d9d9d9;
    --paper: #ffffff;
    --leaf: #5fa22e;
    --forest: #163d10;
    --forest-deep: #0c2208;
    --ink: #3a3a3a;
    --footer: #e9ebe7;
    --photo-warm-1: #e7c9a4;
    --photo-warm-2: #4a3a2a;
    --photo-green-1: #8a8e4e;
    --photo-green-2: #c9a876;
  }
  * { box-sizing: border-box; margin: 0; padding: 0; }
  html, body { width: 1200px; height: 900px; overflow: hidden; }
  body { background: var(--backdrop); font-family: "Lato", sans-serif; position: relative; }

  .page {
    position: absolute; top: 146px; width: 433px; height: 612px;
    background: var(--paper); overflow: hidden;
    box-shadow: 0 2px 6px rgba(0,0,0,.18);
  }
  .page--about { left: 149px; }
  .page--values { left: 623px; background: var(--forest-deep); }

  .page__art { position: absolute; inset: 0; width: 100%; height: 100%; }

  .brand-tab {
    position: absolute; top: 0; right: 0; width: 205px; height: 65px;
    background: var(--paper); border-bottom-left-radius: 60px;
    display: flex; align-items: center; gap: 8px; padding-left: 40px;
  }
  .brand-tab__dot {
    width: 34px; height: 34px; border-radius: 50%;
    border: 3px solid var(--leaf); flex: none;
  }
  .brand-tab__name {
    font-family: "Cinzel", serif; font-weight: 600; font-size: 14px;
    line-height: 1.25; color: var(--forest);
  }

  .about__mark {
    position: absolute; left: 197px; top: 289px; width: 38px; height: 38px;
    border-radius: 50%; border: 3px solid var(--leaf);
  }
  .about__title {
    position: absolute; left: 0; right: 0; top: 333px; text-align: center;
    font-family: "Cinzel", serif; font-weight: 700; font-size: 25px;
    line-height: 32px; color: var(--forest);
  }
  .rule { position: absolute; height: 3px; background: var(--leaf); border-radius: 2px; }
  .about__rule { left: 182px; top: 402px; width: 68px; }
  .about__text {
    position: absolute; left: 24px; right: 24px; top: 423px;
    text-align: center; font-size: 13.4px; line-height: 21.8px; color: var(--ink);
  }

  .values__title {
    position: absolute; left: 21px; top: 311px;
    font-family: "Cinzel", serif; font-weight: 700; font-size: 25px;
    line-height: 31px; color: #fff;
  }
  .values__rule { left: 22px; top: 375px; width: 68px; }
  .value { position: absolute; display: flex; align-items: center; gap: 13px; }
  .value__badge {
    width: 58px; height: 58px; border-radius: 50%; background: #fff; flex: none;
    display: flex; align-items: center; justify-content: center;
  }
  .value__label {
    font-weight: 700; font-size: 12.6px; line-height: 21px; color: #fff;
    text-transform: uppercase;
  }

  .page__footer {
    position: absolute; left: 0; right: 0; bottom: 0; height: 39px;
    background: var(--footer); display: flex; align-items: center;
    padding: 0 22px;
  }
  .page--values .page__footer { background: #f3f4f2; }
  .footer__phone { display: flex; align-items: center; gap: 9px; font-size: 13.5px; color: #222; }
  .footer__social { margin-left: auto; display: flex; gap: 4px; }
  .footer__social span {
    width: 21px; height: 21px; border-radius: 50%;
    border: 2px solid var(--leaf);
  }
</style>
</head>
<body>

<!-- About page -->
<section class="page page--about">
  <svg class="page__art" viewBox="0 0 433 612" preserveAspectRatio="none">
    <defs>
      <linearGradient id="aboutPhoto" x1="0" y1="0" x2="0" y2="1">
        <stop offset="0" stop-color="var(--photo-warm-1)"/>
        <stop offset=".45" stop-color="#b99673"/>
        <stop offset="1" stop-color="var(--photo-warm-2)"/>
      </linearGradient>
    </defs>
    <rect role="img" aria-label="Photo: cupped hands holding a glowing brain outline at sunset" width="433" height="420" fill="url(#aboutPhoto)"/>
    <path d="M0 286 Q150 220 270 250 Q390 290 433 420 L433 612 L0 612 Z" fill="var(--leaf)"/>
    <path d="M0 292 Q150 228 262 258 Q370 290 433 420 L433 612 L0 612 Z" fill="var(--paper)"/>
  </svg>

  <div class="brand-tab">
    <span class="brand-tab__dot"></span>
    <span class="brand-tab__name">Quellarive<br>Care</span>
  </div>

  <span class="about__mark"></span>
  <h1 class="about__title">About<br>Quellarive Care</h1>
  <span class="rule about__rule"></span>
  <p class="about__text">Quellarive Care is different than traditional health practices. Our approach toward health and wellness looks at the whole person and the interaction of each aspect of your being with the other. We have core values that are the backbone of effective integrated care.</p>

  <footer class="page__footer">
    <span class="footer__phone">
      <svg width="12" height="12" viewBox="0 0 24 24"><path fill="var(--leaf)" d="M6.6 10.8a15.1 15.1 0 0 0 6.6 6.6l2.2-2.2c.3-.3.7-.4 1-.2 1.1.4 2.3.6 3.6.6.6 0 1 .4 1 1V20c0 .6-.4 1-1 1A17 17 0 0 1 3 4c0-.6.4-1 1-1h3.5c.6 0 1 .4 1 1 0 1.3.2 2.5.6 3.6.1.3 0 .7-.2 1z"/></svg>
      (615) 555-0147
    </span>
    <span class="footer__social"><span></span><span></span><span></span><span></span><span></span><span></span><span></span></span>
  </footer>
</section>

<!-- Core values page -->
<section class="page page--values">
  <svg class="page__art" viewBox="0 0 433 612" preserveAspectRatio="none">
    <defs>
      <linearGradient id="valuesPhoto" x1="0" y1="0" x2="1" y2="1">
        <stop offset="0" stop-color="var(--photo-green-1)"/>
        <stop offset=".6" stop-color="var(--photo-green-2)"/>
        <stop offset="1" stop-color="#a7864f"/>
      </linearGradient>
      <linearGradient id="valuesPanel" x1="0" y1="0" x2="1" y2="1">
        <stop offset="0" stop-color="var(--forest)"/>
        <stop offset="1" stop-color="var(--forest-deep)"/>
      </linearGradient>
    </defs>
    <rect width="433" height="612" fill="url(#valuesPanel)"/>
    <path role="img" aria-label="Photo: woman in a knit hat breathing fresh air in a forest" d="M0 0 H433 V178 Q330 290 215 286 Q90 282 0 222 Z" fill="url(#valuesPhoto)"/>
    <path d="M0 222 Q90 282 215 286 Q330 290 433 178 L433 190 Q335 296 215 292 Q90 290 0 230 Z" fill="var(--leaf)"/>
  </svg>

  <div class="brand-tab">
    <span class="brand-tab__dot"></span>
    <span class="brand-tab__name">Quellarive<br>Care</span>
  </div>

  <h2 class="values__title">Core Values<br>of Care</h2>
  <span class="rule values__rule"></span>

  <div class="value" style="left:251px;top:316px">
    <span class="value__badge"><svg width="28" height="28" viewBox="0 0 24 24"><path fill="var(--leaf)" d="M12 2a7 7 0 0 0-4 12.7V17h8v-2.3A7 7 0 0 0 12 2zM9 19h6v2H9z"/></svg></span>
    <span class="value__label">Innovative<br>Treatments</span>
  </div>
  <div class="value" style="left:21px;top:395px">
    <span class="value__badge"><svg width="28" height="28" viewBox="0 0 24 24"><path fill="none" stroke="var(--leaf)" stroke-width="2.4" d="M12 20V5M8 8l4-4 4 4M4 14l4-3M20 14l-4-3"/></svg></span>
    <span class="value__label">An Integrative<br>Approach</span>
  </div>
  <div class="value" style="left:251px;top:395px">
    <span class="value__badge"><svg width="28" height="28" viewBox="0 0 24 24"><path fill="none" stroke="var(--leaf)" stroke-width="2.4" d="M12 3v10M12 13l-6 7M12 13l6 7M12 13v8"/></svg></span>
    <span class="value__label">Root Cause<br>Resolution</span>
  </div>
  <div class="value" style="left:21px;top:474px">
    <span class="value__badge"><svg width="28" height="28" viewBox="0 0 24 24"><path fill="var(--leaf)" d="M12 12s-5-3-5-6a2.5 2.5 0 0 1 5-1 2.5 2.5 0 0 1 5 1c0 3-5 6-5 6zM2 16h6l4 2h8v2H11l-4-2H2z"/></svg></span>
    <span class="value__label">Personalized<br>Care</span>
  </div>
  <div class="value" style="left:251px;top:474px">
    <span class="value__badge"><svg width="28" height="28" viewBox="0 0 24 24"><path fill="var(--leaf)" d="M12 20s-8-5-8-11a4 4 0 0 1 8-1 4 4 0 0 1 8 1c0 6-8 11-8 11z"/><path fill="#fff" d="M11 8h2v2h2v2h-2v2h-2v-2H9v-2h2z"/></svg></span>
    <span class="value__label">Co-Creating<br>Health</span>
  </div>

  <footer class="page__footer">
    <span class="footer__phone">
      <svg width="12" height="12" viewBox="0 0 24 24"><path fill="var(--leaf)" d="M6.6 10.8a15.1 15.1 0 0 0 6.6 6.6l2.2-2.2c.3-.3.7-.4 1-.2 1.1.4 2.3.6 3.6.6.6 0 1 .4 1 1V20c0 .6-.4 1-1 1A17 17 0 0 1 3 4c0-.6.4-1 1-1h3.5c.6 0 1 .4 1 1 0 1.3.2 2.5.6 3.6.1.3 0 .7-.2 1z"/></svg>
      (615) 555-0147
    </span>
    <span class="footer__social"><span></span><span></span><span></span><span></span><span></span><span></span><span></span></span>
  </footer>
</section>

</body>
</html>
```